****Business Card Design for Quarrystone Development. Design based around attached logo/company name

I’m looking for business card design for my company Quarrystone Development Group,LLC. Design should be professional, sharp and minimal. Outside of the attached logos, greyscale colors for remainder of cards. My thoughts are two-sided card with attached logo on one side and my info on the other but open to one-sided as well with right design.
Target Market(s)
Real estate professionals including banks, private investors, property owners, developers, commercial tenants like Brewlantern, Grovika or Tanquist’s.
Industry/Entity Type
Commercial real estate development and investments.
Contact Information for Business Card
Name, title, email, phone #’s, web address and physical address
Font styles to use
Other font styles liked:
- Helvetica, Garamond, etc
Colors
Designer to choose only greyscale colors for use in the design.
Requirements
Must have
- Attached logo first or second options.
Nice to have
- Two sided card with logo on one side. Attached Logo/company name can be laid out any way that flows as long as it’s legible.name
Should not have
- No loud colors. ***Please do not include logo, I have removed the company design with a logo image.

```html
<!DOCTYPE html>
<html lang="en">
<head>
<meta charset="utf-8">
<title>Quarrystone Development Group, LLC — Business Card</title>
<link rel="stylesheet" href="https://fonts.googleapis.com/css2?family=Cormorant+Garamond:wght@700&family=Arimo:wght@400&display=swap">
<style>
  :root {
    --backdrop: #1d1e21;
    --card: #5b6475;
    --ink: #f1f2f4;
    --ink-soft: #d9dce2;
    --radius: 26px;
  }
  * { box-sizing: border-box; margin: 0; padding: 0; }
  html, body {
    width: 1200px; height: 948px; overflow: hidden;
    background: var(--backdrop);
  }
  .canvas {
    position: relative; width: 1200px; height: 948px;
    display: flex; flex-direction: column; align-items: center;
    justify-content: center; gap: 56px;
  }
  .card {
    position: relative; width: 640px; height: 366px;
    background: var(--card); border-radius: var(--radius);
    color: var(--ink);
  }

  /* Company name set as plain text */
  .company-name {
    font-family: "Arimo", Helvetica, Arial, sans-serif;
    font-weight: 400; font-style: normal; color: var(--ink);
    letter-spacing: 0.08em; text-transform: uppercase;
    line-height: 1.3;
  }

  /* Front */
  .card--front { display: flex; align-items: center; justify-content: center; }
  .card--front .company-name { font-size: 30px; text-align: center; }

  /* Back */
  .card--back .company-name {
    position: absolute; left: 52px; top: 96px; width: 250px;
    font-size: 17px; text-align: left;
  }

  .address {
    position: absolute; left: 52px; bottom: 62px;
    font-family: "Arimo", Helvetica, Arial, sans-serif;
    font-style: normal;
    font-size: 16px; line-height: 1.45; color: var(--ink);
  }

  .person {
    position: absolute; left: 352px; top: 58px;
  }
  .person__name {
    font-family: "Cormorant Garamond", Garamond, serif;
    font-weight: 700; font-size: 24px; letter-spacing: 0.03em;
    text-transform: uppercase;
  }
  .person__title {
    font-family: "Arimo", Helvetica, Arial, sans-serif;
    font-size: 15px; color: var(--ink-soft); margin-top: 2px;
  }
  .person__rule {
    width: 26px; height: 1px; background: var(--ink); margin-top: 14px;
  }

  .contact {
    position: absolute; left: 352px; top: 196px; list-style: none;
    font-family: "Arimo", Helvetica, Arial, sans-serif;
    font-size: 14px; line-height: 1;
  }
  .contact__item { display: flex; align-items: center; gap: 9px; margin-bottom: 13px; }
  .contact__icon { width: 13px; height: 13px; flex: none; }
</style>
</head>
<body>
<main class="canvas">

  <section class="card card--front" aria-label="Card front">
    <p class="company-name">Quarrystone<br>Development Group, LLC</p>
  </section>

  <section class="card card--back" aria-label="Card back">
    <p class="company-name">Quarrystone<br>Development Group, LLC</p>

    <address class="address">
      2190 Harbor Ledge Road<br>
      Millbrook AB 7841
    </address>

    <div class="person">
      <h1 class="person__name">Daniel Ashworth</h1>
      <p class="person__title">Founder/CEO</p>
      <div class="person__rule"></div>
    </div>

    <ul class="contact">
      <li class="contact__item">
        <svg class="contact__icon" viewBox="0 0 16 16" aria-hidden="true">
          <circle cx="8" cy="8" r="8" fill="var(--ink)"/>
          <path d="M5.2 4.2l1.4-.3.8 1.9-.9.8a5 5 0 0 0 2.9 2.9l.8-.9 1.9.8-.3 1.4c-3.8.2-6.8-2.8-6.6-6.6z" fill="var(--card)"/>
        </svg>
        (555)-310-2846
      </li>
      <li class="contact__item">
        <svg class="contact__icon" viewBox="0 0 16 16" aria-hidden="true">
          <rect x="1" y="3.5" width="14" height="9.5" rx="1" fill="var(--ink)"/>
          <path d="M1.5 4.2L8 9l6.5-4.8" fill="none" stroke="var(--card)" stroke-width="1.2"/>
        </svg>
        info@quarrystonedevelopment.com
      </li>
      <li class="contact__item">
        <svg class="contact__icon" viewBox="0 0 16 16" aria-hidden="true">
          <circle cx="8" cy="8" r="7.5" fill="var(--ink)"/>
          <ellipse cx="8" cy="8" rx="3" ry="7" fill="none" stroke="var(--card)" stroke-width="1"/>
          <path d="M1 8h14M2.2 4.5h11.6M2.2 11.5h11.6" stroke="var(--card)" stroke-width="1"/>
        </svg>
        www.quarrystonedevelopment.com
      </li>
    </ul>
  </section>

</main>
</body>
</html>
```